Business Card Design Project

We need a new fresh business card for our business. There are multiple services we offer and we need a fresh corporate card that represents us better. We start from cleaning carpet and tiles, to upholstery and curtains, to completely clean all contents and building materials after a fire, or completely dry out a home or business after a major or minor flood event. We are open to all concepts as we want to create a new look, maybe even logo, signage, vehicle signage, uniforms.
We are open to new colours etc.

Go to www.brolvaquincare.com.au for current logo and all other past ideas

Target Market(s)

Everyone is our possible client but we are targeting more coorporate

Industry/Entity Type

Building

```html
<!DOCTYPE html>
<html lang="en">
<head>
<meta charset="utf-8">
<title>Brolvaquin Care – Business Card</title>
<link rel="stylesheet" href="https://fonts.googleapis.com/css2?family=Montserrat:wght@500;700&family=Open+Sans:wght@400;600&display=swap">
<style>
  :root {
    --blue: #1d5fa3;
    --pink: #e0197d;
    --paper: #f7f7f8;
    --paper-shade: #e4e5e8;
    --violet: #5b4aa8;
    --ink: #4a4a55;
    --backdrop: #ecebe8;
  }
  * { margin: 0; padding: 0; box-sizing: border-box; }
  html, body { width: 1200px; height: 828px; overflow: hidden; }
  body {
    background: var(--backdrop);
    font-family: "Open Sans", Arial, sans-serif;
    position: relative;
  }
  .card {
    position: absolute;
    top: 264px;
    width: 520px;
    height: 300px;
    background: linear-gradient(135deg, var(--paper) 40%, var(--paper-shade) 100%);
    box-shadow: 0 6px 18px rgba(0,0,0,0.15);
    overflow: hidden;
  }
  .card--front { left: 50px; }
  .card--back { left: 630px; }
  .card .swoosh { position: absolute; inset: 0; width: 100%; height: 100%; }
  .brand {
    position: absolute;
    display: flex;
    align-items: center;
    gap: 10px;
  }
  .card--front .brand { left: 52px; top: 128px; }
  .card--back .brand { left: 52px; top: 100px; }
  .brand__name {
    font-family: "Montserrat", Arial, sans-serif;
    font-weight: 700;
    font-size: 24px;
    color: var(--blue);
    letter-spacing: 0.2px;
  }
  .brand__dot {
    width: 38px; height: 38px;
    border-radius: 50%;
    background: var(--pink);
  }
  .card--back .brand__name { font-size: 20px; }
  .card--back .brand__dot { width: 32px; height: 32px; }
  .person {
    position: absolute;
    left: 52px;
    bottom: 46px;
  }
  .person__name {
    font-family: "Montserrat", Arial, sans-serif;
    font-weight: 500;
    font-size: 16px;
    color: var(--violet);
    letter-spacing: 0.5px;
  }
  .person__role {
    font-size: 10px;
    color: var(--ink);
    margin-top: 2px;
  }
  .contacts {
    position: absolute;
    left: 368px;
    top: 112px;
    list-style: none;
    color: #fff;
    font-size: 8.5px;
  }
  .contacts li {
    display: flex;
    align-items: center;
    gap: 6px;
    margin-bottom: 9px;
    white-space: nowrap;
  }
  .contacts svg { width: 12px; height: 12px; flex: none; }
</style>
</head>
<body>

<section class="card card--front" aria-label="Card front">
  <svg class="swoosh" viewBox="0 0 520 300" aria-hidden="true">
    <path d="M450,0 C410,130 300,240 70,300 L520,300 L520,0 Z" fill="var(--blue)"/>
    <path d="M418,0 C380,130 280,232 78,300" fill="none" stroke="var(--pink)" stroke-width="9"/>
    <path d="M488,0 C470,70 440,120 392,162 C432,112 456,62 470,0 Z" fill="var(--pink)"/>
  </svg>
  <div class="brand">
    <span class="brand__name">Brolvaquin Care</span>
    <span class="brand__dot"></span>
  </div>
</section>

<section class="card card--back" aria-label="Card back">
  <svg class="swoosh" viewBox="0 0 520 300" aria-hidden="true">
    <path d="M370,0 C346,120 310,222 244,300 L520,300 L520,0 Z" fill="var(--blue)"/>
    <path d="M340,0 C320,120 280,224 210,300" fill="none" stroke="var(--pink)" stroke-width="12"/>
    <path d="M440,0 C430,45 414,80 392,104 C408,76 418,42 422,0 Z" fill="var(--pink)"/>
  </svg>
  <div class="brand">
    <span class="brand__name">Brolvaquin Care</span>
    <span class="brand__dot"></span>
  </div>
  <div class="person">
    <p class="person__name">MARCUS TELLFORD</p>
    <p class="person__role">Managing Director</p>
  </div>
  <ul class="contacts">
    <li>
      <svg viewBox="0 0 12 12"><circle cx="6" cy="6" r="6" fill="#fff"/><path d="M4 3.2 L5.2 4.6 L4.6 5.4 Q5.4 6.8 6.6 7.4 L7.4 6.8 L8.8 8 L8 9 Q5 8.6 3.2 4 Z" fill="var(--blue)"/></svg>
      <span>012 345 6789</span>
    </li>
    <li>
      <svg viewBox="0 0 12 12"><circle cx="6" cy="6" r="6" fill="#fff"/><path d="M4 3.2 L5.2 4.6 L4.6 5.4 Q5.4 6.8 6.6 7.4 L7.4 6.8 L8.8 8 L8 9 Q5 8.6 3.2 4 Z" fill="var(--blue)"/></svg>
      <span>012 345 6790</span>
    </li>
    <li>
      <svg viewBox="0 0 12 12"><circle cx="6" cy="6" r="6" fill="#fff"/><rect x="3" y="4" width="6" height="4.2" fill="none" stroke="var(--blue)" stroke-width="0.9"/><path d="M3 4 L6 6.4 L9 4" fill="none" stroke="var(--blue)" stroke-width="0.9"/></svg>
      <span>hello@brolvaquincare.com.au</span>
    </li>
    <li>
      <svg viewBox="0 0 12 12"><circle cx="6" cy="6" r="6" fill="#fff"/><circle cx="6" cy="6" r="3.2" fill="none" stroke="var(--blue)" stroke-width="0.9"/><path d="M2.8 6 H9.2 M6 2.8 Q4.4 6 6 9.2 M6 2.8 Q7.6 6 6 9.2" fill="none" stroke="var(--blue)" stroke-width="0.7"/></svg>
      <span>www.brolvaquincare.com.au</span>
    </li>
    <li>
      <svg viewBox="0 0 12 12"><circle cx="6" cy="6" r="6" fill="#fff"/><path d="M6 9.4 C4 7 3.6 6 3.6 5 A2.4 2.4 0 0 1 8.4 5 C8.4 6 8 7 6 9.4 Z" fill="var(--blue)"/><circle cx="6" cy="5" r="0.9" fill="#fff"/></svg>
      <span>12 Harbour Street, Sydney NSW</span>
    </li>
  </ul>
</section>

</body>
</html>
```